Create a business promotion flyer to leave in customer mailboxes. We are a bulk petroleum supplier, servicing any industry that requires diesel. Base in griffith NSW, servicing griffith area and surrounds.

Business Name - Terra Diesel
Fuel@terradiesel-example.com.au
Owen - 0491 570 362 ohartley@terradiesel-example.com.au
Liam - 0491 570 718 lprosser@terradiesel-example.com.au
Simon - 0491 570 905 skenway@terradiesel-example.com.au
Office 02 5550 1734

Bulk Fuel deliveries.
Oils & lubricants
Local Family owned business

```html
<!DOCTYPE html>
<html lang="en">
<head>
<meta charset="utf-8">
<title>Terra Diesel – Bulk Fuel Flyer</title>
<link href="https://fonts.googleapis.com/css2?family=Barlow+Condensed:wght@600;700&family=Source+Sans+3:wght@400;600&family=Allura&display=swap" rel="stylesheet">
<style>
  :root {
    --black: #111111;
    --ink: #1a1a1a;
    --paper: #ecebe8;
    --red: #c0211d;
    --red-deep: #b01f1b;
    --white: #ffffff;
    --grey-line: #5a5a5a;
    --divider: #9a9a9a;
    --text-soft: #d9d9d9;
  }
  * { margin: 0; padding: 0; box-sizing: border-box; }
  html, body { width: 800px; height: 1200px; overflow: hidden; background: var(--black); }
  .flyer {
    position: relative; width: 800px; height: 1200px; overflow: hidden;
    background: var(--black); color: var(--white);
    font-family: "Source Sans 3", Arial, sans-serif;
  }
  .backdrop, .hero-photo { position: absolute; inset: 0; width: 800px; height: 1200px; }
  .abs { position: absolute; }
  .headline-font { font-family: "Barlow Condensed", "Arial Narrow", sans-serif; font-weight: 700; }

  .brand-name { left: 32px; top: 96px; font-size: 60px; font-weight: 600; color: var(--red); letter-spacing: -0.5px; line-height: 1; }
  .tagline { left: 30px; top: 171px; font-size: 17px; font-weight: 600; letter-spacing: 0.2px; }

  .hero-title { left: 32px; top: 226px; line-height: 0.95; text-transform: uppercase; }
  .hero-title .line-1 { display: block; font-size: 78px; }
  .hero-title .line-2 { display: block; font-size: 56px; margin-top: 2px; }
  .hero-title .line-3 { display: block; font-size: 56px; color: var(--red); margin-top: 2px; }
  .hero-intro { left: 32px; top: 434px; font-size: 19px; line-height: 28px; color: var(--text-soft); }

  .service { top: 564px; width: 220px; text-align: center; color: var(--ink); }
  .service svg { display: block; margin: 0 auto; }
  .service h2 { font-family: "Barlow Condensed", "Arial Narrow", sans-serif; font-weight: 700; font-size: 21px; line-height: 24px; margin-top: 18px; text-transform: uppercase; }
  .service p { font-size: 14.5px; line-height: 21.5px; margin-top: 12px; }
  .service-divider { top: 566px; width: 1px; height: 214px; background: var(--divider); }

  .contact-title { left: 36px; top: 842px; font-size: 29px; line-height: 1; }
  .contact-sub { left: 36px; top: 876px; font-size: 20px; color: var(--red); line-height: 1; }
  .contact-list { left: 36px; top: 910px; width: 402px; list-style: none; }
  .contact-row { display: flex; align-items: center; height: 36px; border-bottom: 1px solid #3a3a3a; font-size: 14px; }
  .contact-row:last-child { border-bottom: none; }
  .contact-row svg { flex: 0 0 18px; }
  .contact-name { width: 66px; margin-left: 14px; font-weight: 600; font-size: 15px; }
  .contact-phone { width: 110px; font-size: 14.5px; }
  .contact-email { font-size: 12px; white-space: nowrap; }

  .promise-script { left: 528px; top: 882px; font-family: "Allura", cursive; font-size: 44px; line-height: 44px; color: var(--white); }
  .promise-line { left: 528px; top: 984px; font-size: 23px; line-height: 24px; text-transform: uppercase; }

  .footer-rule { left: 36px; top: 1097px; width: 729px; height: 1px; background: var(--grey-line); }
  .value { top: 1118px; display: flex; align-items: center; gap: 12px; }
  .value h3 { font-family: "Barlow Condensed", "Arial Narrow", sans-serif; font-weight: 700; font-size: 15px; line-height: 17px; text-transform: uppercase; }
  .value p { font-size: 11.5px; color: var(--text-soft); line-height: 16px; }
  .value-divider { top: 1121px; width: 1px; height: 38px; background: var(--grey-line); }
</style>
</head>
<body>
<main class="flyer">

  <svg class="backdrop" viewBox="0 0 800 1200" aria-hidden="true">
    <polygon points="0,553 800,490 800,812 436,815 0,800" fill="var(--paper)"/>
    <polygon points="436,815 800,812 800,1086 505,1086" fill="var(--red-deep)"/>
  </svg>

  <svg class="hero-photo" viewBox="0 0 800 1200" role="img" aria-label="Photo of a white fuel tanker truck on a rural road under gum trees and blue sky">
    <defs>
      <linearGradient id="photoTone" x1="0" y1="0" x2="0" y2="1">
        <stop offset="0" stop-color="#4f86c6"/>
        <stop offset="0.35" stop-color="#9fbfdf"/>
        <stop offset="0.55" stop-color="#6f7c5a"/>
        <stop offset="0.8" stop-color="#3a3d3a"/>
        <stop offset="1" stop-color="#262626"/>
      </linearGradient>
    </defs>
    <polygon points="418,0 800,0 800,490 510,510 301,281" fill="url(#photoTone)"/>
    <polyline points="418,0 301,281 510,510" fill="none" stroke="var(--red)" stroke-width="2.5"/>
  </svg>

  <div class="abs brand-name">Terra Diesel</div>
  <div class="abs tagline">RELIABLE. LOCAL. READY TO DELIVER.</div>

  <h1 class="abs hero-title headline-font">
    <span class="line-1">Fuel</span>
    <span class="line-2">That Keeps</span>
    <span class="line-3">You Moving</span>
  </h1>
  <p class="abs hero-intro">Proudly supplying bulk fuel and<br>lubricants to Griffith and surrounds.</p>

  <section class="abs service" style="left:28px">
    <svg width="52" height="62" viewBox="0 0 52 62" aria-hidden="true">
      <rect x="4" y="2" width="30" height="56" rx="4" fill="var(--red)"/>
      <rect x="0" y="54" width="38" height="7" rx="2" fill="var(--red)"/>
      <rect x="10" y="9" width="18" height="14" rx="2" fill="none" stroke="var(--paper)" stroke-width="2.5"/>
      <circle cx="19" cy="38" r="5" fill="none" stroke="var(--paper)" stroke-width="2.5"/>
      <path d="M34 14 L42 20 V46 a4 4 0 0 0 8 0 V24 L46 18" fill="none" stroke="var(--red)" stroke-width="2.5"/>
    </svg>
    <h2>Bulk Fuel<br>Deliveries</h2>
    <p>Reliable on-time<br>deliveries of<br>premium diesel.</p>
  </section>
  <div class="abs service-divider" style="left:265px"></div>

  <section class="abs service" style="left:286px">
    <svg width="52" height="62" viewBox="0 0 52 62" aria-hidden="true">
      <path d="M26 3 C18 16 5 28 5 40 a21 21 0 0 0 42 0 C47 28 34 16 26 3 Z" fill="none" stroke="var(--red)" stroke-width="2.5"/>
      <path d="M17 40 a9 9 0 0 0 18 0" fill="none" stroke="var(--red)" stroke-width="2.5"/>
      <path d="M20 30 C22 26 24 23 26 20" fill="none" stroke="var(--red)" stroke-width="2.5"/>
    </svg>
    <h2>Oils &amp;<br>Lubricants</h2>
    <p>Quality products<br>to keep your<br>equipment<br>performing.</p>
  </section>
  <div class="abs service-divider" style="left:517px"></div>

  <section class="abs service" style="left:531px">
    <svg width="70" height="62" viewBox="0 0 70 62" aria-hidden="true">
      <circle cx="35" cy="16" r="12" fill="none" stroke="var(--red)" stroke-width="2.5"/>
      <path d="M14 58 V50 a13 13 0 0 1 13 -13 H43 a13 13 0 0 1 13 13 V58 Z" fill="none" stroke="var(--red)" stroke-width="2.5"/>
      <path d="M20 12 a9 9 0 0 0 -2 17 M50 12 a9 9 0 0 1 2 17" fill="none" stroke="var(--red)" stroke-width="2.5"/>
      <path d="M12 33 a10 10 0 0 0 -9 10 V50 H10 M58 33 a10 10 0 0 1 9 10 V50 H60" fill="none" stroke="var(--red)" stroke-width="2.5"/>
    </svg>
    <h2>Local. Family<br>Owned.</h2>
    <p>Proudly local,<br>personally committed<br>to our community<br>and customers.</p>
  </section>

  <h2 class="abs contact-title headline-font">CONTACT OUR TEAM</h2>
  <p class="abs contact-sub headline-font">WE’RE HERE TO HELP.</p>

  <ul class="abs contact-list">
    <li class="contact-row">
      <svg width="18" height="18" viewBox="0 0 18 18" aria-hidden="true"><circle cx="9" cy="5" r="4.5" fill="var(--red)"/><path d="M1 18 V15 a5 5 0 0 1 5 -5 H12 a5 5 0 0 1 5 5 V18 Z" fill="var(--red)"/></svg>
      <span class="contact-name">Owen</span><span class="contact-phone">0491 570 362</span><span class="contact-email">ohartley@terradiesel-example.com.au</span>
    </li>
    <li class="contact-row">
      <svg width="18" height="18" viewBox="0 0 18 18" aria-hidden="true"><circle cx="9" cy="5" r="4.5" fill="var(--red)"/><path d="M1 18 V15 a5 5 0 0 1 5 -5 H12 a5 5 0 0 1 5 5 V18 Z" fill="var(--red)"/></svg>
      <span class="contact-name">Liam</span><span class="contact-phone">0491 570 718</span><span class="contact-email">lprosser@terradiesel-example.com.au</span>
    </li>
    <li class="contact-row">
      <svg width="18" height="18" viewBox="0 0 18 18" aria-hidden="true"><circle cx="9" cy="5" r="4.5" fill="var(--red)"/><path d="M1 18 V15 a5 5 0 0 1 5 -5 H12 a5 5 0 0 1 5 5 V18 Z" fill="var(--red)"/></svg>
      <span class="contact-name">Simon</span><span class="contact-phone">0491 570 905</span><span class="contact-email">skenway@terradiesel-example.com.au</span>
    </li>
    <li class="contact-row">
      <svg width="18" height="18" viewBox="0 0 18 18" aria-hidden="true"><path d="M4 1 L7 5 L5.5 7.5 C6.5 10 8 11.5 10.5 12.5 L13 11 L17 14 L15 17 C8 17 1 10 1 3 Z" fill="var(--red)"/></svg>
      <span class="contact-name">Office</span><span class="contact-phone">02 5550 1734</span><span class="contact-email">Fuel@terradiesel-example.com.au</span>
    </li>
  </ul>

  <p class="abs promise-script">Locally owned.<br>Locally invested.</p>
  <p class="abs promise-line headline-font">Fueling<br>Our Community.</p>

  <div class="abs footer-rule"></div>

  <div class="abs value" style="left:36px">
    <svg width="30" height="36" viewBox="0 0 30 36" aria-hidden="true"><path d="M15 2 L28 7 V17 C28 26 22 31 15 34 C8 31 2 26 2 17 V7 Z" fill="none" stroke="var(--white)" stroke-width="2.2"/><path d="M9 18 L13.5 22.5 L21 14" fill="none" stroke="var(--white)" stroke-width="2.2"/></svg>
    <div><h3>Reliable</h3><p>You can count on us.</p></div>
  </div>
  <div class="abs value-divider" style="left:203px"></div>

  <div class="abs value" style="left:232px">
    <svg width="34" height="34" viewBox="0 0 34 34" aria-hidden="true"><circle cx="17" cy="17" r="15" fill="none" stroke="var(--white)" stroke-width="2.2"/><path d="M17 8 V17 L23 21" fill="none" stroke="var(--white)" stroke-width="2.2"/></svg>
    <div><h3>On Time</h3><p>When you need it.</p></div>
  </div>
  <div class="abs value-divider" style="left:394px"></div>

  <div class="abs value" style="left:424px">
    <svg width="26" height="36" viewBox="0 0 26 36" aria-hidden="true"><path d="M13 2 C8 11 2 18 2 24 a11 11 0 0 0 22 0 C24 18 18 11 13 2 Z" fill="none" stroke="var(--white)" stroke-width="2.2"/><path d="M7 25 a6 6 0 0 0 6 6" fill="none" stroke="var(--white)" stroke-width="2"/></svg>
    <div><h3>Quality</h3><p>Fuel you can trust.</p></div>
  </div>
  <div class="abs value-divider" style="left:582px"></div>

  <div class="abs value" style="left:612px">
    <svg width="28" height="36" viewBox="0 0 28 36" aria-hidden="true"><path d="M14 34 C6 24 2 18 2 13 a12 12 0 0 1 24 0 C26 18 22 24 14 34 Z" fill="none" stroke="var(--white)" stroke-width="2.2"/><circle cx="14" cy="13" r="4.5" fill="none" stroke="var(--white)" stroke-width="2.2"/></svg>
    <div><h3>Local</h3><p>Proudly Griffith.</p></div>
  </div>

</main>
</body>
</html>
```